Fenwick Grading LTD - website for irrigation & Landscape Lighting & Buried service wire

Looking for a website to help promote my business with Irrigation (installation, service, etc) and buried service wire/drainage solutions.

Commercial/Residential

Landscape lighting.

I’ll get photos in the trucks and trailers to upload as well maybe the machine as well.

Target Market(s)

Homeowners who want green grass and beautiful gardens. Beautiful landscape lighting

Industry/Entity Type

Irrigation systems and landscape lighting and buried service wire to homes and offering Drainage soltions.

Coding

Coded - Design and coding required

Number of Pages Required

4 page

Colors
F0912C
F2A743
F7CA91
FBE8D2
FDF5EE

Requirements
Must have
• was hoping to link up my email on fenwickgrading@mailbox-example.net with the website if possible.
Nice to have
• Page for Irrigation, page for landscape lighting, page buried service wire & drainage soltions.

```html
<!DOCTYPE html>
<html lang="en">
<head>
<meta charset="utf-8">
<title>Fenwick Grading LTD – Irrigation & Landscape Lighting</title>
<link href="https://fonts.googleapis.com/css2?family=Montserrat:wght@400;500;600;700&family=Oswald:wght@500;600&display=swap" rel="stylesheet">
<style>
:root{
  --orange:#f0912c;
  --orange-2:#f2a743;
  --sand:#f7ca91;
  --cream:#fbe8d2;
  --cream-light:#fdf5ee;
  --ink:#1d1d1d;
  --text:#4a4a4a;
  --white:#ffffff;
  --footer:#1c1f1b;
}
*{margin:0;padding:0;box-sizing:border-box}
html,body{width:1200px;height:4132px;overflow:hidden;background:var(--white)}
body{position:relative;font-family:"Montserrat",sans-serif;color:var(--text)}
.abs{position:absolute}
a{color:inherit;text-decoration:none}

/* hero */
.hero-bg{left:0;top:0;width:1200px;height:625px}
.brand{left:141px;top:22px;color:var(--orange);font-weight:700;font-size:22px;line-height:26px;letter-spacing:1px;white-space:nowrap}
.brand small{display:block;color:var(--white);font-size:12px;font-weight:600;letter-spacing:2px;line-height:16px}
.brand-mark{display:inline-block;width:14px;height:14px;background:var(--orange);margin-right:8px;vertical-align:1px}
.nav{left:510px;top:27px;width:550px;display:flex;align-items:center;height:36px;font-size:12px;font-weight:500;color:var(--white);white-space:nowrap}
.nav a{margin-right:29px}
.nav .nav-cta{position:absolute;left:444px;top:0;width:106px;height:36px;margin:0;background:var(--orange);display:flex;align-items:center;justify-content:center;white-space:nowrap;font-size:11.5px}
.hero-title{left:141px;top:178px;width:520px;font-family:"Oswald",sans-serif;font-weight:600;font-size:37px;line-height:49px;color:var(--white)}
.hero-text{left:141px;top:336px;width:450px;font-size:12px;line-height:22.5px;color:var(--white)}
.btn-square{background:var(--orange);color:var(--white);font-size:12px;font-weight:500;display:flex;align-items:center;justify-content:center;white-space:nowrap}
.hero-btn{left:141px;top:417px;width:104px;height:37px}

/* section shared */
.mark{width:26px;height:14px;background:var(--orange);border-radius:2px}
.section-title{font-size:25px;font-weight:600;color:var(--ink);line-height:32px;white-space:nowrap}
.section-title span{color:var(--orange)}
.lead{border-left:2px solid var(--orange);padding-left:11px;font-size:12.5px;font-weight:500;color:var(--ink);line-height:22.5px}
.copy{font-size:12.5px;line-height:22.5px;color:var(--text)}
.pill-btn{background:var(--orange);color:var(--white);font-size:11.5px;font-weight:600;letter-spacing:1px;border-radius:20px;display:flex;align-items:center;justify-content:center;height:33px;white-space:nowrap}

/* about */
.photo{background:linear-gradient(160deg,#3d4a2a,#9a6a2c 55%,#2f3a22)}
.card{background:var(--white);border-radius:8px;box-shadow:0 4px 18px rgba(0,0,0,.15);padding:8px}
.card .photo{width:100%;height:100%;border-radius:6px}
.phone{display:flex;align-items:center;font-size:14px;font-weight:600;color:var(--ink);white-space:nowrap}
.phone .ring{width:34px;height:34px;border:1.5px solid var(--orange);border-radius:50%;display:flex;align-items:center;justify-content:center;margin-right:12px}

/* testimonial */
.quote{left:220px;top:2933px;width:760px;text-align:center;font-size:12.5px;line-height:22.5px;color:var(--ink)}
.client-name{color:var(--orange);font-size:14.5px;font-weight:500}
.client-role{font-size:12.5px;color:var(--text);margin-top:4px}

/* contact */
.contact-box{left:141px;top:3184px;width:918px;height:549px;background:var(--cream);border-radius:18px}
.field{background:var(--white);border-radius:5px;font-size:11.5px;color:#777;padding:0 21px;display:flex;align-items:center}
.field.area{align-items:flex-start;padding-top:15px}

/* footer */
.footer{left:0;top:3818px;width:1200px;height:314px;background:linear-gradient(120deg,#20241d,#2d2a1f 60%,#1a1c18)}
.f-head{color:var(--orange);font-size:15px;font-weight:500}
.f-list{font-size:12.5px;color:var(--white);line-height:27.5px;margin-top:12px;list-style:none;white-space:nowrap}
.f-contact{font-size:12.5px;color:var(--white);line-height:20px}
.f-contact li{list-style:none;display:flex;margin-bottom:14px}
.f-contact svg{flex:none;margin-right:12px;margin-top:2px}
.copyright{left:141px;top:4094px;font-size:12px;color:var(--white)}
.social{left:925px;top:4091px;display:flex;gap:11px}
.social span{width:25px;height:25px;border-radius:50%;background:var(--orange)}
</style>
</head>
<body>

<!-- HERO -->
<svg class="abs hero-bg" viewBox="0 0 1200 625" role="img" aria-label="Evening garden with lawn, planted beds and glowing path lights">
  <defs>
    <linearGradient id="heroGrad" x1="0" y1="0" x2="1" y2="1">
      <stop offset="0" stop-color="#1f2a17"/>
      <stop offset=".45" stop-color="#3c5224"/>
      <stop offset=".8" stop-color="#5a4a22"/>
      <stop offset="1" stop-color="#2a2a16"/>
    </linearGradient>
    <linearGradient id="heroShade" x1="0" x2="1">
      <stop offset="0" stop-color="#000" stop-opacity=".45"/>
      <stop offset=".6" stop-color="#000" stop-opacity=".05"/>
    </linearGradient>
  </defs>
  <path d="M0 0H1200V540C900 545 760 560 600 618C440 560 300 545 0 540Z" fill="url(#heroGrad)"/>
  <path d="M0 0H1200V540C900 545 760 560 600 618C440 560 300 545 0 540Z" fill="url(#heroShade)"/>
  <path d="M0 540C300 545 440 560 600 618C760 560 900 545 1200 540" fill="none" stroke="var(--orange)" stroke-width="3"/>
</svg>

<div class="abs brand"><span class="brand-mark"></span>FENWICK<small>GRADING LTD</small></div>
<nav class="abs nav">
  <a href="#">Home</a><a href="#">Irrigation</a><a href="#">Landscape Lighting</a><a href="#">Fiber Optic Installation</a>
  <a class="nav-cta" href="#">Contact Us</a>
</nav>
<h1 class="abs hero-title">Transform Your Outdoor Space With Our Expert Irrigation And Lighting Solutions</h1>
<p class="abs hero-text">Get the perfect blend of form and function with our state-of-the-art irrigation systems and landscape lighting.Trust our experienced team to deliver top-notch fiber optic installation for your home</p>
<a class="abs btn-square hero-btn" href="#">Contact Us</a>

<!-- ABOUT -->
<div class="abs photo" style="left:244px;top:730px;width:229px;height:372px;border-radius:115px 115px 0 115px;background:linear-gradient(160deg,#2e3320,#8a5a22 45%,#d4963e 60%,#3a3a24)" role="img" aria-label="Lawn sprinkler spraying water at sunset"></div>
<div class="abs" style="left:256px;top:730px;width:229px;height:372px;border:1.5px solid var(--orange);border-radius:115px 115px 0 115px;border-left:none;border-top:none"></div>
<div class="abs card" style="left:211px;top:721px;width:82px;height:92px"><div class="photo" style="background:linear-gradient(160deg,#8aa84a,#3d6a2a)" role="img" aria-label="Close-up of grass being watered"></div></div>
<div class="abs card" style="left:141px;top:925px;width:137px;height:159px"><div class="photo" style="background:linear-gradient(150deg,#6f8a3a,#a89a6a 50%,#4a6a2a)" role="img" aria-label="Sprinkler watering a garden bed"></div></div>
<div class="abs card" style="left:458px;top:940px;width:120px;height:111px;display:flex;align-items:center;justify-content:center"><span style="width:40px;height:40px;background:var(--orange);border-radius:4px"></span></div>

<div class="abs mark" style="left:638px;top:741px"></div>
<h2 class="abs section-title" style="left:638px;top:775px"><span>About</span> Fenwick Grading</h2>
<p class="abs copy" style="left:638px;top:829px;width:410px">Welcome to our professional irrigation systems and landscape lighting services. We specialize in providing homeowners with lush green lawns, vibrant gardens, and captivating outdoor lighting.</p>
<p class="abs copy" style="left:638px;top:933px;width:420px">With our expertise in irrigation installation, service, landscape lighting, and fiber optic installation, we can transform your home into a stunning oasis. Discover the possibilities and enhance the beauty of your outdoor spaces with our top-notch services.</p>
<a class="abs pill-btn" href="#" style="left:638px;top:1051px;width:123px">LEARN MORE</a>
<div class="abs phone" style="left:778px;top:1050px">
  <span class="ring"><svg width="16" height="16" viewBox="0 0 24 24"><path d="M6.6 10.8a15.1 15.1 0 0 0 6.6 6.6l2.2-2.2c.3-.3.7-.4 1-.2 1.1.4 2.3.6 3.6.6.6 0 1 .4 1 1V20c0 .6-.4 1-1 1A17 17 0 0 1 3 4c0-.6.4-1 1-1h3.5c.6 0 1 .4 1 1 0 1.2.2 2.4.6 3.6.1.3 0 .7-.2 1z" fill="var(--orange)"/></svg></span>
  123-456-7890
</div>

<!-- IRRIGATION BAND -->
<svg class="abs" style="left:0;top:1170px" width="1200" height="530" viewBox="0 0 1200 530">
  <path d="M0 9C200 40 330 50 600 28C850 8 1000 0 1200 15V452C1000 470 850 470 600 500C350 530 180 520 0 490Z" fill="var(--cream)"/>
</svg>
<div class="abs mark" style="left:141px;top:1259px"></div>
<h2 class="abs section-title" style="left:141px;top:1294px">Irrigation <span>Systems</span></h2>
<p class="abs lead" style="left:141px;top:1348px;width:400px">Efficient and Effective Watering Solutions for Your Lawn and Garden</p>
<p class="abs copy" style="left:141px;top:1408px;width:420px">Our irrigation systems are designed to provide your lawn and garden with the right amount of water, without wasting a single drop. With our expert installation and service, you can rest assured that your plants will receive the nourishment they need to thrive.</p>
<a class="abs pill-btn" href="#" style="left:141px;top:1547px;width:123px">LEARN MORE</a>
<svg class="abs" style="left:662px;top:1245px" width="395" height="385" viewBox="0 0 395 385" role="img" aria-label="Agricultural sprinkler head spraying water over a field">
  <defs><linearGradient id="g1" x1="0" y1="0" x2="0" y2="1"><stop offset="0" stop-color="#b9cad6"/><stop offset=".55" stop-color="#8a9aa0"/><stop offset="1" stop-color="#4b5a3a"/></linearGradient></defs>
  <path d="M250 12C330 30 382 130 372 215C362 300 280 360 180 372C80 384 8 330 8 250C8 160 80 70 150 32C185 14 220 6 250 12Z" fill="url(#g1)"/>
  <path d="M262 5C345 28 392 132 381 218C370 305 285 368 182 378C90 388 25 350 12 270" fill="none" stroke="var(--orange)" stroke-width="1.5"/>
</svg>

<!-- LANDSCAPE LIGHTING -->
<svg class="abs" style="left:150px;top:1775px" width="385" height="385" viewBox="0 0 385 385" role="img" aria-label="Landscaped garden at dusk with lit bollard path lights">
  <defs><linearGradient id="g2" x1="0" y1="0" x2="1" y2="1"><stop offset="0" stop-color="#2c3a1c"/><stop offset=".5" stop-color="#7a7a2a"/><stop offset="1" stop-color="#3a4a1e"/></linearGradient></defs>
  <path d="M120 12C200-5 300 40 350 120C390 190 360 290 270 330C180 370 60 375 20 300C-10 240 10 150 50 80C70 45 90 20 120 12Z" fill="url(#g2)"/>
  <path d="M128 6C210-8 312 40 362 125C400 198 368 300 276 340C190 378 80 382 28 320" fill="none" stroke="var(--orange)" stroke-width="1.5"/>
</svg>
<div class="abs mark" style="left:626px;top:1787px"></div>
<h2 class="abs section-title" style="left:626px;top:1822px">Landscape <span>Lighting</span></h2>
<p class="abs lead" style="left:626px;top:1876px;width:420px">Enhance Your Outdoor Space with Beautiful and Functional Lighting Solutions</p>
<p class="abs copy" style="left:626px;top:1936px;width:420px">Our landscape lighting solutions are designed to enhance the beauty and functionality of your outdoor space. From subtle pathway lighting to dramatic spotlights, we'll work with you to create a lighting plan that meets your needs and complements your landscape.</p>
<a class="abs pill-btn" href="#" style="left:626px;top:2075px;width:123px">LEARN MORE</a>

<!-- FIBER OPTIC BAND -->
<svg class="abs" style="left:0;top:2225px" width="1200" height="540" viewBox="0 0 1200 540">
  <path d="M0 22C250 10 420 38 650 25C900 10 1050 0 1200 5V460C1000 480 850 478 600 500C350 525 150 500 0 470Z" fill="var(--cream)"/>
</svg>
<div class="abs mark" style="left:141px;top:2337px"></div>
<h2 class="abs section-title" style="left:141px;top:2372px">Fiber Optic <span>Installation</span></h2>
<p class="abs lead" style="left:141px;top:2427px;width:420px">Expert Installation of Fiber Optic Networks for Your Home</p>
<p class="abs copy" style="left:141px;top:2465px;width:420px">Our team of experienced professionals will install your fiber optic network with precision and care. We'll work with you to ensure that your home is equipped with the latest technology, providing you with fast and reliable internet, TV, and voice services.</p>
<a class="abs pill-btn" href="#" style="left:141px;top:2580px;width:123px">LEARN MORE</a>
<svg class="abs" style="left:662px;top:2305px" width="395" height="385" viewBox="0 0 395 385" role="img" aria-label="Technician testing white cables with an orange multimeter on a table">
  <defs><linearGradient id="g3" x1="0" y1="0" x2="1" y2="1"><stop offset="0" stop-color="#e6e2dc"/><stop offset=".45" stop-color="#8a5a3a"/><stop offset="1" stop-color="#2a1e18"/></linearGradient></defs>
  <path d="M250 12C330 30 382 130 372 215C362 300 280 360 180 372C80 384 8 330 8 250C8 160 80 70 150 32C185 14 220 6 250 12Z" fill="url(#g3)"/>
  <path d="M262 5C345 28 392 132 381 218C370 305 285 368 182 378C90 388 25 350 12 270" fill="none" stroke="var(--orange)" stroke-width="1.5"/>
</svg>

<!-- TESTIMONIAL -->
<div class="abs mark" style="left:587px;top:2848px"></div>
<h2 class="abs section-title" style="left:0;width:1200px;text-align:center;top:2874px">What Our <span>Client</span> Say</h2>
<p class="abs quote">“ Dana Whitlow is a Strategist, Author and Disability &amp; STEM Advocate who has dedicated her life to serving others. Dana Founded Brightfold in 2014, a leading digital strategy studio, as well as Clearpath Labs in 2019, a technology firm committed to bridging the accessibility gap in product development. ”</p>
<svg class="abs" style="left:278px;top:3060px" width="38" height="16" viewBox="0 0 38 16"><path d="M37 8H2M9 1L2 8l7 7" fill="none" stroke="var(--ink)" stroke-width="1.5"/></svg>
<svg class="abs" style="left:885px;top:3060px" width="38" height="16" viewBox="0 0 38 16"><path d="M1 8h35M29 1l7 7-7 7" fill="none" stroke="var(--ink)" stroke-width="1.5"/></svg>
<div class="abs" style="left:511px;top:3038px;width:61px;height:61px;border-radius:50%;background:linear-gradient(160deg,#c9ccd0,#6a6e74)" role="img" aria-label="Client portrait"></div>
<div class="abs" style="left:593px;top:3047px"><div class="client-name">Marcus Reed</div><div class="client-role">Web Designer</div></div>

<!-- CONTACT -->
<section class="abs contact-box"></section>
<div class="abs mark" style="left:587px;top:3234px"></div>
<h2 class="abs section-title" style="left:0;width:1200px;text-align:center;top:3263px">Contact <span>Us</span></h2>
<p class="abs copy" style="left:0;width:1200px;text-align:center;top:3312px">Complete the form below to schedule your meeting with Fenwick Grading</p>
<div class="abs field" style="left:217px;top:3376px;width:373px;height:42px">First name</div>
<div class="abs field" style="left:608px;top:3376px;width:374px;height:42px">Email</div>
<div class="abs field" style="left:217px;top:3437px;width:373px;height:42px">Phone</div>
<div class="abs field" style="left:608px;top:3437px;width:374px;height:42px">Question</div>
<div class="abs field area" style="left:217px;top:3497px;width:765px;height:138px">Message</div>
<a class="abs pill-btn" href="#" style="left:539px;top:3665px;width:122px">SUBMIT NOW</a>

<!-- FOOTER -->
<footer class="abs footer" role="img" aria-label="Dark evening garden backdrop"></footer>
<div class="abs brand" style="top:3924px;font-size:34px;line-height:38px"><span class="brand-mark" style="width:20px;height:20px"></span>FENWICK<small style="font-size:18px;line-height:22px">GRADING LTD</small></div>
<div class="abs" style="left:459px;top:3880px"><div class="f-head">Quick Links</div><ul class="f-list"><li>Home</li><li>Irrigation</li><li>Landscape Lighting</li><li>Fiber Optic Installation</li></ul></div>
<div class="abs" style="left:670px;top:3880px"><div class="f-head">Useful Links</div><ul class="f-list"><li>Contact</li><li>Privacy Policy</li><li>Terms of Service</li></ul></div>
<div class="abs" style="left:839px;top:3880px;width:320px"><div class="f-head">Contact Info</div>
  <ul class="f-contact" style="margin-top:16px">
    <li><svg width="16" height="18" viewBox="0 0 24 24"><path d="M12 2a7 7 0 0 0-7 7c0 5 7 13 7 13s7-8 7-13a7 7 0 0 0-7-7zm0 9.5A2.5 2.5 0 1 1 12 6.5a2.5 2.5 0 0 1 0 5z" fill="var(--orange)"/></svg><span>Address Line 1, Address<br>Line 2, Address Line 3.</span></li>
    <li><svg width="16" height="14" viewBox="0 0 24 20"><path d="M2 2h20v16H2z" fill="var(--orange)"/><path d="M2 3l10 8 10-8" fill="none" stroke="#1f221c" stroke-width="2"/></svg><span style="font-size:12px;white-space:nowrap">fenwickgrading@mailbox-example.net</span></li>
    <li><svg width="16" height="16" viewBox="0 0 24 24"><path d="M6.6 10.8a15.1 15.1 0 0 0 6.6 6.6l2.2-2.2c.3-.3.7-.4 1-.2 1.1.4 2.3.6 3.6.6.6 0 1 .4 1 1V20c0 .6-.4 1-1 1A17 17 0 0 1 3 4c0-.6.4-1 1-1h3.5c.6 0 1 .4 1 1 0 1.2.2 2.4.6 3.6.1.3 0 .7-.2 1z" fill="var(--orange)"/></svg><span>123-456-7890</span></li>
  </ul>
</div>
<div class="abs" style="left:141px;top:4075px;width:918px;height:1px;background:rgba(255,255,255,.15)"></div>
<p class="abs copyright">© 2024 Fenwick Grading. All rights reserved.</p>
<div class="abs social"><span></span><span></span><span></span><span></span></div>

</body>
</html>
```